Commercial Refrigeration Service Company requires stylish and fresh looking flyer.

We need a flyer to hand out to new customers. It should have a photo and our branding, list all the services that are offered and our contact details.
We would like two flyers to be supplied, both identical though one offering a discount until July ( Half Price Service Fee ). The flyer should be clear, interesting and in similar colours to the branding package supplied.
Please look at our website for information about the services on offer:
www.brisko-coolworks.com.au

Target Market(s)

Cafes, bars, restaurants, pubs ect.

Font styles to use
Other font styles liked:
• Font package provided

Colors
85cae6
ffffff
333333

Requirements
Must have
• - The photo provided.
• - The company logo.
• - Similar feel to the website & business card.
• - Smooth layout and clear to understand.
Should not have
• - No clunky badges or prints.

```html
<!DOCTYPE html>
<html lang="en">
<head>
<meta charset="utf-8">
<title>Brisko Commercial Refrigeration – Flyer</title>
<link rel="stylesheet" href="https://fonts.googleapis.com/css2?family=Catamaran:wght@500;600;700&family=Roboto+Condensed:wght@300;400;700&display=swap">
<style>
  :root {
    --brand-blue: #5bc2ea;
    --brand-blue-soft: #85cae6;
    --ink: #333333;
    --paper: #f1f1f1;
    --paper-shade: #e4e4e4;
    --white: #ffffff;
    --stage: #4a4a4a;
  }
  * { margin: 0; padding: 0; box-sizing: border-box; }
  html, body {
    width: 1200px; height: 1146px; overflow: hidden;
    background: var(--stage);
  }
  .flyer {
    position: absolute; left: 200px; top: 7px;
    width: 800px; height: 1131px;
    background: linear-gradient(180deg, var(--paper) 0%, var(--paper-shade) 100%);
    overflow: hidden;
    color: var(--ink);
  }
  .hero-photo {
    position: absolute; left: 0; top: 0; width: 800px; height: 379px;
    background: linear-gradient(180deg, #9cc3e0 0%, #c9d9e6 30%, #8a9096 55%, #6f7378 100%);
  }
  .brand-band {
    position: absolute; left: 0; top: 379px; width: 800px; height: 159px;
    background: var(--brand-blue);
    display: flex; align-items: center; justify-content: center;
  }
  .brand-name {
    font-family: "Catamaran", sans-serif; font-weight: 600;
    font-size: 60px; line-height: 1;
    color: var(--ink);
  }
  .tagline {
    position: absolute; left: 0; right: 0; top: 566px; text-align: center;
    font-family: "Catamaran", sans-serif; font-weight: 500;
    font-size: 24px; line-height: 1.2; color: var(--ink);
  }
  .services-title {
    position: absolute; left: 46px; top: 636px;
    font-family: "Catamaran", sans-serif; font-weight: 700; font-size: 25px;
    display: flex; align-items: center; gap: 14px;
  }
  .services-title svg { margin-top: 4px; }
  .service-list { position: absolute; left: 0; top: 686px; width: 457px; list-style: none; }
  .service-item {
    height: 45.2px; border-bottom: 3px solid var(--white);
    background: linear-gradient(90deg, var(--brand-blue) 0%, var(--brand-blue-soft) 55%, rgba(133,202,230,0) 100%);
    display: flex; align-items: center; gap: 10px; padding-left: 23px;
    font-family: "Catamaran", sans-serif; font-weight: 600; font-size: 21px;
    color: var(--white); text-transform: uppercase;
  }
  .service-item:last-child { border-bottom: 0; }
  .offer-badge { position: absolute; left: 454px; top: 688px; }
  .offer-text {
    position: absolute; left: 454px; top: 688px; width: 316px; height: 316px;
    display: flex; flex-direction: column; align-items: center; justify-content: center;
    color: var(--white); text-align: center; font-family: "Roboto Condensed", sans-serif;
  }
  .offer-head { font-weight: 700; font-size: 37px; line-height: 1; }
  .offer-until { font-weight: 300; font-size: 41px; line-height: 1.05; letter-spacing: 0.02em; }
  .offer-detail { margin-top: 10px; font-weight: 300; font-size: 17px; line-height: 1.3; }
  .contact {
    position: absolute; left: 0; right: 0; top: 1034px; text-align: center;
    font-family: "Roboto Condensed", sans-serif; font-weight: 300; font-size: 16.5px;
    line-height: 21px; color: var(--ink);
  }
  .contact-web {
    margin-top: 3px; font-weight: 700; font-size: 23px; letter-spacing: 0.1em;
    color: var(--brand-blue);
  }
</style>
</head>
<body>
<main class="flyer">
  <div class="hero-photo" role="img" aria-label="Photo of a technician standing beside the company service ute parked at a beachside car park"></div>

  <header class="brand-band">
    <div class="brand-name">Brisko</div>
  </header>

  <div class="tagline">Commercial Refrigeration</div>

  <h2 class="services-title">OUR SERVICES
    <svg width="64" height="10" viewBox="0 0 64 10" aria-hidden="true">
      <g fill="none" stroke="#5bc2ea" stroke-width="1.5">
        <path d="M5 1 L9 5 L5 9 L1 5 Z"/><path d="M32 1 L36 5 L32 9 L28 5 Z"/><path d="M59 1 L63 5 L59 9 L55 5 Z"/>
      </g>
    </svg>
  </h2>

  <ul class="service-list">
    <li class="service-item"><svg width="13" height="13" viewBox="0 0 13 13" aria-hidden="true"><path d="M6.5 1 L12 6.5 L6.5 12 L1 6.5 Z" fill="none" stroke="#fff" stroke-width="2"/></svg>Commercial Refrigeration</li>
    <li class="service-item"><svg width="13" height="13" viewBox="0 0 13 13" aria-hidden="true"><path d="M6.5 1 L12 6.5 L6.5 12 L1 6.5 Z" fill="none" stroke="#fff" stroke-width="2"/></svg>Ice Makers</li>
    <li class="service-item"><svg width="13" height="13" viewBox="0 0 13 13" aria-hidden="true"><path d="M6.5 1 L12 6.5 L6.5 12 L1 6.5 Z" fill="none" stroke="#fff" stroke-width="2"/></svg>Beer Systems</li>
    <li class="service-item"><svg width="13" height="13" viewBox="0 0 13 13" aria-hidden="true"><path d="M6.5 1 L12 6.5 L6.5 12 L1 6.5 Z" fill="none" stroke="#fff" stroke-width="2"/></svg>Electrical</li>
    <li class="service-item"><svg width="13" height="13" viewBox="0 0 13 13" aria-hidden="true"><path d="M6.5 1 L12 6.5 L6.5 12 L1 6.5 Z" fill="none" stroke="#fff" stroke-width="2"/></svg>24hr Service</li>
    <li class="service-item"><svg width="13" height="13" viewBox="0 0 13 13" aria-hidden="true"><path d="M6.5 1 L12 6.5 L6.5 12 L1 6.5 Z" fill="none" stroke="#fff" stroke-width="2"/></svg>Sales</li>
    <li class="service-item"><svg width="13" height="13" viewBox="0 0 13 13" aria-hidden="true"><path d="M6.5 1 L12 6.5 L6.5 12 L1 6.5 Z" fill="none" stroke="#fff" stroke-width="2"/></svg>Installation</li>
  </ul>

  <svg class="offer-badge" width="316" height="316" viewBox="0 0 316 316" aria-hidden="true">
    <path d="M158 2 L314 158 L158 314 L2 158 Z" fill="none" stroke="#5bc2ea" stroke-width="3"/>
    <path d="M158 10 L306 158 L158 306 L10 158 Z" fill="#5bc2ea"/>
  </svg>
  <div class="offer-text">
    <div class="offer-head">DISCOUNT</div>
    <div class="offer-until">UNTIL JULY</div>
    <div class="offer-detail">PAY ONLY HALF PRICE<br>OF THE SERVICE FEE</div>
  </div>

  <footer class="contact">
    <div>PO Box 1180 Seabreeze NSW 2099 | 0400 128 764</div>
    <div>info@brisko-coolworks.com.au | ABN: 41 502 337 918 | Licence No: 418273C</div>
    <div class="contact-web">WWW.BRISKO-COOLWORKS.COM.AU</div>
  </footer>
</main>
</body>
</html>
```